New Business Cards for Tormin Group

We need a new Business Card to compliment our new logo. We are a vibrant design, manufacture and install business providing recreation areas, public parks and Municipal spaces. We want business cards that are classy, modern and clean.

We have recently changed our logo, and are celebrating our 40th anniversary. We want business cards with a new modern design to reflect our status.

Target Market(s)

Customers

Contact Information for Business Card

We need all the details of our 3 offices as per the business card attached. Please disregard the old logo on the business card, the other three files show our new logo.

Requirements
Must have
• All info as per attached business card but with new logo.
Nice to have

```html
<!DOCTYPE html>
<html lang="en">
<head>
<meta charset="utf-8">
<title>Tormin Group – Business Card</title>
<link href="https://fonts.googleapis.com/css2?family=Lato:wght@400;700&display=swap" rel="stylesheet">
<style>
  :root {
    --backdrop: #1f1f1f;
    --card: #ffffff;
    --accent: #e8313a;
    --ink: #333333;
    --muted: #555555;
    --rule: #3a3a3a;
    --band: #4a4a4a;
    --decor: #f1f1f1;
    --brand: #444444;
  }
  * { margin: 0; padding: 0; box-sizing: border-box; }
  html, body {
    width: 1200px; height: 900px; overflow: hidden;
    background: var(--backdrop);
    font-family: "Lato", sans-serif;
  }
  .card {
    position: absolute; left: 260px; top: 257px;
    width: 680px; height: 386px;
    background: var(--card);
    border-radius: 22px;
    overflow: hidden;
  }
  .decor-globe {
    position: absolute; left: 391px; top: -64px;
    width: 282px; height: 282px; border-radius: 50%;
    background: var(--decor);
  }
  .brand {
    position: absolute; left: 462px; top: 70px;
    display: flex; align-items: center; gap: 8px;
  }
  .brand-dot {
    width: 16px; height: 16px; border-radius: 50%;
    background: var(--accent);
  }
  .brand-name {
    font-weight: 700; font-size: 21px; letter-spacing: 1px;
    color: var(--brand); white-space: nowrap;
  }
  .name-tab {
    position: absolute; left: 0; top: 73px;
    width: 15px; height: 46px;
    background: var(--accent);
    border-radius: 0 4px 4px 0;
  }
  .person-name {
    position: absolute; left: 29px; top: 67px;
    font-size: 25px; font-weight: 700; color: var(--accent);
  }
  .person-role {
    position: absolute; left: 29px; top: 100px;
    font-size: 16.5px; color: var(--ink);
  }
  .direct {
    position: absolute; left: 29px; top: 160px;
    font-size: 14px; color: var(--ink); line-height: 26.5px;
  }
  .direct .label { color: var(--accent); }
  .divider {
    position: absolute; left: 29px; top: 217px;
    width: 616px; height: 1.5px; background: var(--rule);
  }
  .office {
    position: absolute; top: 230px;
    font-size: 13.4px; color: var(--muted); line-height: 20.2px;
    white-space: nowrap;
  }
  .office h2 {
    font-size: 16.5px; font-weight: 400; color: var(--accent);
    margin-bottom: 3px; line-height: 22px;
  }
  .office--head { left: 29px; }
  .office--dubai { left: 262px; }
  .office--qatar { left: 476px; top: 232px; line-height: 19.2px; }
  .footer-band {
    position: absolute; left: 0; bottom: 0;
    width: 100%; height: 15px; background: var(--band);
  }
  .web-tab {
    position: absolute; left: 0; top: 0; width: 680px; height: 386px;
  }
  .web-address {
    position: absolute; left: 0; top: 356px; width: 662px;
    text-align: center; font-size: 16.5px; color: #ffffff;
  }
</style>
</head>
<body>
  <div class="card">
    <div class="decor-globe" role="img" aria-label="Faint world globe decoration"></div>

    <div class="brand">
      <span class="brand-dot"></span>
      <span class="brand-name">TORMIN GROUP</span>
    </div>

    <span class="name-tab"></span>
    <h1 class="person-name">Sami Haddar</h1>
    <p class="person-role">Managing Partner</p>

    <div class="direct">
      <p><span class="label">Phone</span>: +971 (0)50 438 7190</p>
      <p><span class="label">Email</span>: sami@tormingroup.com</p>
    </div>

    <div class="divider"></div>

    <section class="office office--head">
      <h2>Head Office</h2>
      <p>P.O. Box: 31842 Abu Dhabi. U.A.E</p>
      <p>Tel No: +971 (0)2 5128470</p>
      <p>Fax No: +971(0)2 5128471</p>
      <p>Email: sales@tormingroup.com</p>
    </section>

    <section class="office office--dubai">
      <h2>Dubai Office</h2>
      <p>P.O. Box: 471206 Dubai, U.A.E</p>
      <p>Tel No: +971 (0)4 382614</p>
      <p>Fax No: +971(0)4 382655</p>
      <p>Email: sales@tormingroup.com</p>
    </section>

    <section class="office office--qatar">
      <h2>Qater Office</h2>
      <p>P.O. Box: 20937 Doha, Qatter</p>
      <p>Tel No: +974 44718302</p>
      <p>Fax No: +971 44613587</p>
      <p>Email: sales@tormingroup.com</p>
    </section>

    <div class="footer-band"></div>
    <svg class="web-tab" viewBox="0 0 680 386" aria-hidden="true">
      <polygon points="222,349 461,349 481,386 201,386" fill="#e8313a"/>
    </svg>
    <p class="web-address">www.tormingroup.com</p>
  </div>
</body>
</html>
```